Brand Identity Stationary Package

Hello I'm looking for a full branding package for my Property Management Company. I have a logo but looking to have the following
Business Card
Email signature
Facebook cover photo
Letterhead (word.doc)
#10 Envelope
Pocket Folder - link to 9x12 pocket folder design specs https://www.printorbit-example.ca/marketing-materials/presentation-folders
would like everything to match and be brand identifiable. The company looks after residential properties/apartments and some commercial properties. Attached is a zip of the files.
For Business Card
Name: Gareth Lindqvist
Position: Operations Manager
Number: 1 (555) 384-2917
Email: Gareth@harborkey-example.ca
Website: Harborkey-example.ca
Property Management

```html
<!DOCTYPE html>
<html lang="en">
<head>
<meta charset="UTF-8">
<title>Harborkey Property Management – Business Card</title>
<link href="https://fonts.googleapis.com/css2?family=Inter:wght@400;500;600;700&display=swap" rel="stylesheet">
<style>
  :root {
    --page-bg: #e4e4e4;
    --card-white: #ffffff;
    --ink: #141414;
    --brand-green: #76a832;
    --deco-grey: #e6e6e6;
    --dark-card-top: #585858;
    --dark-card-bottom: #262626;
    --emboss: #d2d2d2;
  }
  * { box-sizing: border-box; margin: 0; padding: 0; }
  html, body {
    width: 1200px; height: 1200px; overflow: hidden;
    background: var(--page-bg);
    font-family: "Inter", Arial, sans-serif;
    color: var(--ink);
  }
  .canvas { position: relative; width: 1200px; height: 1200px; }

  .card {
    position: absolute; left: 262px; width: 686px; height: 392px;
    border-radius: 20px; overflow: hidden;
  }
  .card-front { top: 165px; background: var(--card-white); }
  .card-back {
    top: 653px;
    background: linear-gradient(200deg, var(--dark-card-top) 0%, #3a3a3a 45%, var(--dark-card-bottom) 100%);
  }

  .roof-decoration {
    position: absolute; left: 0; top: 117px; width: 497px; height: 258px;
    background: linear-gradient(115deg, var(--deco-grey) 0%, #efefef 55%, rgba(255,255,255,0) 100%);
  }

  .front-brand { position: absolute; right: 50px; top: 50px; text-align: right; }
  .brand-name {
    font-weight: 700; font-size: 40px; letter-spacing: 3px; line-height: 1;
    color: var(--ink);
  }
  .brand-tagline {
    margin-top: 10px; font-size: 11px; font-weight: 500;
    letter-spacing: 6.2px; margin-right: -6px;
  }

  .accent-bar {
    position: absolute; left: 0; top: 228px; width: 12px; height: 46px;
    background: var(--brand-green);
  }
  .person { position: absolute; left: 46px; top: 222px; }
  .person-name { font-size: 30px; font-weight: 700; line-height: 1; letter-spacing: 0.2px; }
  .person-role { margin-top: 3px; font-size: 17.5px; font-weight: 500; color: var(--brand-green); }

  .divider {
    position: absolute; left: 46px; right: 50px; top: 288px;
    height: 1.5px; background: var(--ink);
  }

  .contact { position: absolute; left: 46px; top: 305px; list-style: none; font-size: 17px; }
  .contact li { display: flex; align-items: center; gap: 9px; height: 22px; }
  .contact .phone { font-weight: 600; }
  .contact svg { width: 13px; height: 13px; flex: none; }

  .website {
    position: absolute; right: 50px; top: 326px;
    font-size: 17px; font-weight: 600;
  }
  .website .domain-suffix { color: var(--brand-green); }

  .band-black {
    position: absolute; left: 0; bottom: 0; width: 237px; height: 17px; background: var(--ink);
  }
  .band-green {
    position: absolute; left: 246px; right: 0; bottom: 0; height: 17px; background: var(--brand-green);
  }

  .back-brand {
    position: absolute; left: 0; right: 0; top: 150px; text-align: center; color: var(--emboss);
  }
  .back-brand .brand-name { font-size: 64px; letter-spacing: 5px; color: var(--emboss); }
  .back-brand .brand-tagline {
    margin-top: 14px; font-size: 17px; letter-spacing: 11px; margin-right: -11px; font-weight: 400;
  }
</style>
</head>
<body>
<main class="canvas">

  <section class="card card-front" aria-label="Business card front">
    <div class="roof-decoration" role="img" aria-label="Faint grey house roofline decoration"></div>

    <header class="front-brand">
      <div class="brand-name">HARBORKEY</div>
      <div class="brand-tagline">PROPERTY MANAGEMENT</div>
    </header>

    <div class="accent-bar"></div>
    <div class="person">
      <h1 class="person-name">GARETH LINDQVIST</h1>
      <p class="person-role">Operations Manager</p>
    </div>

    <div class="divider"></div>

    <ul class="contact">
      <li class="phone">
        <svg viewBox="0 0 24 24" aria-hidden="true"><path fill="#76a832" d="M6.6 10.8c1.4 2.8 3.8 5.1 6.6 6.6l2.2-2.2c.3-.3.7-.4 1-.2 1.1.4 2.3.6 3.6.6.6 0 1 .4 1 1V20c0 .6-.4 1-1 1C10.6 21 3 13.4 3 4c0-.6.4-1 1-1h3.5c.6 0 1 .4 1 1 0 1.3.2 2.5.6 3.6.1.3 0 .7-.2 1z"/></svg>
        1 (555) 384-2917
      </li>
      <li class="email">
        <svg viewBox="0 0 24 24" aria-hidden="true"><rect x="2" y="5" width="20" height="14" rx="1" fill="#76a832"/><path d="M3 6l9 7 9-7" fill="none" stroke="#fff" stroke-width="1.8"/></svg>
        Gareth@harborkey-example.ca
      </li>
    </ul>

    <div class="website">Harborkey<span class="domain-suffix">-example.ca</span></div>

    <div class="band-black"></div>
    <div class="band-green"></div>
  </section>

  <section class="card card-back" aria-label="Business card back">
    <div class="back-brand">
      <div class="brand-name">HARBORKEY</div>
      <div class="brand-tagline">PROPERTY MANAGEMENT</div>
    </div>
  </section>

</main>
</body>
</html>
```